Lone Star Wetland Flora Stewardship Guild

We need to design the home page of this new website. We would like a fun website design for provides as a resource for members and information for potential members.
Please design so that we can see a portion of background on each side on the website.
I just need the final design files psd no coding needed.
Attached is their logo (colors are not 100% set in stone either so can mess with those as I did in the quick mockup attached)
Attached is a pdf newsletter they send out, you can get a feel for them and what they are about. The design is crappy and we are here to fix that going forward and we are starting with the website.
Here are some quick example websites (design style is open)
- I attached a quick mockup i did just for a content visual but by all means do what you want.
- http://www.brightpathleaders.example/
- http://www.civicunityhub.example/
- http://preview.webskinvault.example/show.php?cat=layouts&host=skinbazaar&temp=novaline
- http://www.meadowkeep.example/
- http://www.urbangleaners.example/
- http://www.projectcozyknit.example/
here are some of the other chapters website (pretty bad!)
and here are some of the others:
- http://www.dwrvcs.example/
- http://kwfg.example/
- http://www.blvcg.example/
Content Items that need to be included:
1. Logo
2. Menu - home, about, members, resources, events, membership, contact
3. Become a member - button or action
4. social links - chatterloop, workweave, clipstream
5. banner - that needs to explain their purpose "Promoting environmental stewardship through operations, research, education and outreach" (or this can be worked into the design)
6. Upcoming event (s)
7. Advertisement - members can place an ad on the website, this can be a placeholder for now
8. newsletter signup
9. advertise with us - this link can be in the footer
30-60 years of age, succesfull (household budgets of 120K+ men and women that live in texas.
Education

```html
<!DOCTYPE html>
<html lang="en">
<head>
<meta charset="utf-8">
<title>Lone Star Wetland Flora Stewardship Guild</title>
<link href="https://fonts.googleapis.com/css2?family=Source+Sans+3:ital,wght@0,400;0,600;0,700;1,600&display=swap" rel="stylesheet">
<style>
:root{
  --navy:#0b3f8f;
  --navy-dark:#07306f;
  --red:#d8404f;
  --text:#6d6d6d;
  --panel:#f7f9fc;
  --line:#d9dde3;
  --white:#ffffff;
  --banner-top:#6f9cc6;
  --banner-bottom:#5b8a6a;
  --reed-green:#6f9658;
  --lily-green:#5f8872;
  --ad-blue:#7fb0cc;
  --ad-grey:#e6e9ee;
}
*{margin:0;padding:0;box-sizing:border-box}
html,body{width:1005px;height:1200px;overflow:hidden}
body{font-family:"Source Sans 3",sans-serif;position:relative;background:var(--navy-dark)}
.backdrop{position:absolute;inset:0;background:linear-gradient(180deg,#dde8f1 0%,#8fb0c6 35%,#1f5aa6 62%,#0d4596 100%)}
.page{position:absolute;left:110px;top:0;width:784px;height:1105px;background:var(--panel)}
.nav{position:absolute;left:0;top:0;width:784px;height:54px;display:flex;background:linear-gradient(#e76171,#d24051);border-bottom:1px solid #c93a4a}
.nav a{color:#fff;text-decoration:none;font-size:13.5px;display:flex;align-items:center;justify-content:center;border-right:1px solid #c7394a;height:54px}
.nav a.active{background:linear-gradient(#1d58ae,#0b3f8f)}
.brand{position:absolute;left:28px;top:82px;display:flex;align-items:center;gap:8px}
.brand-mark{width:18px;height:18px;background:var(--red)}
.brand-name{font-size:14px;font-weight:700;color:var(--navy);line-height:1.15;width:150px}
.social{position:absolute;left:420px;top:78px;display:flex;gap:10px}
.social span{display:flex;align-items:center;gap:3px;font-size:10px;font-weight:600;color:var(--navy)}
.social i{width:8px;height:8px;border-radius:50%;background:var(--red);display:block}
.join{position:absolute;left:620px;top:72px;width:140px;height:29px;border-radius:15px;background:linear-gradient(#2a68c0,#0b3f8f);color:#fff;font-size:11px;font-weight:700;display:flex;align-items:center;padding-left:15px;gap:10px;box-shadow:0 1px 2px rgba(0,0,0,.3)}
.chev{width:13px;height:13px;border-radius:50%;background:#072a60;display:flex;align-items:center;justify-content:center}
.search{position:absolute;left:494px;top:120px;width:266px;height:36px;background:#fff;box-shadow:0 1px 4px rgba(0,0,0,.2);padding:6px 7px;display:flex;gap:5px}
.search .field{flex:1;border:1px solid #ccc;border-radius:3px;display:flex;align-items:center;padding-left:4px}
.search .go{width:50px;background:linear-gradient(#e23a3a,#b81f24);color:#fff;font-size:10px;font-weight:700;display:flex;align-items:center;justify-content:center;border-radius:2px}
.banner{position:absolute;left:26px;top:177px;width:734px;height:356px;background:linear-gradient(180deg,var(--banner-top),var(--banner-bottom))}
.banner-text{position:absolute;left:0;right:0;top:229px;text-align:center;color:#fff;font-size:22px;line-height:31px;text-shadow:0 1px 3px rgba(0,0,0,.45)}
.banner-text b{font-weight:700}
.dots{position:absolute;left:329px;top:324px;display:flex;gap:6px}
.dots i{width:10px;height:10px;border-radius:50%;background:#fff;border:2px solid #1d4f92;display:block}
.dots i.on{background:var(--red);border-color:#fff}
.welcome{position:absolute;left:26px;top:572px;width:510px}
h2{font-size:19.5px;font-weight:700;color:var(--navy)}
h2 em{font-style:normal;color:var(--red)}
.lead{margin-top:18px;font-size:13px;color:var(--navy)}
.body-copy{margin-top:12px;font-size:10px;line-height:18px;color:var(--text)}
.more{margin-top:14px;width:128px;height:32px;border-radius:16px;background:linear-gradient(#ef7a8c,#d9485e);color:#fff;font-size:11px;font-weight:600;display:flex;align-items:center;justify-content:center;box-shadow:0 1px 2px rgba(0,0,0,.25)}
.rule{position:absolute;left:26px;top:794px;width:508px;border-top:1px solid var(--line)}
.events-head{position:absolute;left:26px;top:818px;width:508px;display:flex;justify-content:space-between;align-items:center}
.arrows{display:flex;gap:3px}
.event{position:absolute;top:862px;width:241px}
.event .photo{height:128px;border:3px solid #fff;box-shadow:0 0 0 1px #ddd}
.event .p1{background:var(--reed-green)}
.event .p2{background:var(--lily-green)}
.event .meta{display:flex;gap:10px;margin-top:12px}
.date{width:48px;height:48px;flex:none;background:#e9e9e9;border-radius:2px;overflow:hidden;text-align:center}
.date small{display:block;background:var(--red);color:#fff;font-size:7px;line-height:9px}
.date b{font-size:27px;line-height:36px;color:#111}
.event p{font-size:10px;line-height:15px;color:#8a8a8a}
.event p a{color:var(--navy);font-style:italic;font-weight:600;text-decoration:none}
.ad{position:absolute;left:568px;top:578px;width:192px;height:256px;background:linear-gradient(180deg,var(--ad-blue),var(--ad-grey));border:1px solid #d8dde3}
.news{position:absolute;left:568px;top:862px;width:192px;height:188px;border:1px solid #d8dde3;background:#f2f4f7}
.news-head{height:37px;background:linear-gradient(#e35a69,#d13f50);color:#fff;font-size:16.5px;font-weight:700;display:flex;align-items:center;justify-content:center}
.news-copy{font-size:8.5px;line-height:11px;color:#9a9a9a;padding:9px 7px 0 8px}
.news-field{margin:7px 7px 0;height:26px;background:#fff;border:1px solid #dcdcdc;font-size:9.5px;color:#555;padding-left:7px;display:flex;align-items:center}
.news-field + .news-field{margin-top:8px}
.signup{margin:10px auto 0;width:142px;height:30px;border-radius:15px;background:linear-gradient(#2a68c0,#0b3f8f);color:#fff;font-size:11px;font-weight:700;display:flex;align-items:center;justify-content:center;gap:22px;padding-left:14px}
.footer{position:absolute;left:108px;top:1126px;width:790px;color:#fff;font-size:11px}
.footer .adv{position:absolute;left:3px;top:2px;font-size:12.5px;font-weight:600;text-decoration:underline}
.footer .links{position:absolute;right:2px;top:3px;font-size:10.5px}
.footer .addr{position:absolute;left:0;top:27px;font-size:10.5px}
.footer .copy{position:absolute;right:0;top:27px;font-size:10px}
</style>
</head>
<body>
<div class="backdrop" role="img" aria-label="Lake scene with lily pads and trees fading into deep blue water"></div>

<div class="page">
  <nav class="nav">
    <a class="active" style="width:96px">HOME</a>
    <a style="width:99px">ABOUT</a>
    <a style="width:110px">MEMBERS</a>
    <a style="width:122px">RESOURCES</a>
    <a style="width:103px">EVENTS</a>
    <a style="width:134px">MEMBERSHIP</a>
    <a style="width:120px;border-right:0">CONTACT</a>
  </nav>

  <div class="brand">
    <span class="brand-mark"></span>
    <span class="brand-name">Lone Star Wetland Flora Stewardship Guild</span>
  </div>

  <div class="social">
    <span><i></i>chatterloop</span>
    <span><i></i>workweave</span>
    <span><i></i>clipstream</span>
  </div>

  <div class="join">BECOME A MEMBER
    <span class="chev"><svg width="7" height="5" viewBox="0 0 7 5"><path d="M0 0h7L3.5 5z" fill="#fff"/></svg></span>
  </div>

  <div class="search">
    <div class="field"><svg width="10" height="10" viewBox="0 0 10 10"><circle cx="4" cy="4" r="3" fill="none" stroke="#666" stroke-width="1.2"/><path d="M6.2 6.2L9.5 9.5" stroke="#666" stroke-width="1.4"/></svg></div>
    <div class="go">SEARCH</div>
  </div>

  <div class="banner" role="img" aria-label="Wide wetland landscape photograph with river, marsh and cloudy sky">
    <div class="banner-text">PROMOTING ENVIRONMENTAL STEWARDSHIP THROUGH<br><b>OPERATIONS, RESEARCH, EDUCATION</b> AND <b>OUTREACH</b></div>
    <div class="dots"><i></i><i class="on"></i><i></i><i></i><i></i></div>
  </div>

  <section class="welcome">
    <h2>WELCOME <em>TO OUR SITE!!</em></h2>
    <p class="lead">Sed ut perspiciatis unde omnis iste natus error sit voluptatem accusantium ;</p>
    <p class="body-copy">Sed ut perspiciatis unde omnis iste natus error sit voluptatem accusantium doloremque laudantium, totam rem aperiam, eaque ipsa quae ab illo inventore veritatis et quasi architecto beatae vitae dicta sunt explicabo. Nemo enim ipsam voluptatem quia voluptas sit aspernatur aut odit aut fugit, sed quia consequuntur magni dolores eos qui ratione voluptatem sequi nesciunt.</p>
    <div class="more">MORE INFORMATION</div>
  </section>

  <div class="rule"></div>

  <div class="events-head">
    <h2>UPCOMING <em>EVENT (S)</em></h2>
    <div class="arrows">
      <svg width="15" height="15" viewBox="0 0 15 15"><circle cx="7.5" cy="7.5" r="7.5" fill="#777"/><path d="M9 4L5 7.5 9 11z" fill="#fff"/></svg>
      <svg width="15" height="15" viewBox="0 0 15 15"><circle cx="7.5" cy="7.5" r="7.5" fill="#0b3f8f"/><path d="M6 4l4 3.5L6 11z" fill="#fff"/></svg>
    </div>
  </div>

  <article class="event" style="left:26px">
    <div class="photo p1" role="img" aria-label="Event photograph of a pond edged with tall reeds"></div>
    <div class="meta">
      <div class="date"><small>Monday</small><b>23</b></div>
      <p>Sed ut perspiciatis unde omnis iste natbj us error sit voluptatem accusantium loremfg doloremque laudantium,..........<a>Read More</a></p>
    </div>
  </article>

  <article class="event" style="left:293px">
    <div class="photo p2" role="img" aria-label="Event photograph of water lily pads among reeds"></div>
    <div class="meta">
      <div class="date"><small>Monday</small><b>23</b></div>
      <p>Sed ut perspiciatis unde omnis iste natbj us error sit voluptatem accusantium loremfg doloremque laudantium,..........<a>Read More</a></p>
    </div>
  </article>

  <aside class="ad" role="img" aria-label="Member advertisement placeholder for water treatment products"></aside>

  <aside class="news">
    <div class="news-head">NEWSLETTER SIGNUP</div>
    <p class="news-copy">Sed ut perspiciatis unde omnis iste natus erro sit voluptatem accusantium</p>
    <div class="news-field">Name:</div>
    <div class="news-field">Email:</div>
    <div class="signup">SIGNUP HERE <span class="chev"><svg width="7" height="5" viewBox="0 0 7 5"><path d="M0 0h7L3.5 5z" fill="#fff"/></svg></span></div>
  </aside>
</div>

<footer class="footer">
  <span class="adv">ADVERTISE WITH US</span>
  <span class="links">HOME &nbsp;// &nbsp;ABOUT // &nbsp;MEMBERS // &nbsp;RESOURCES // &nbsp;EVENTS // &nbsp;MEMBERSHIP // &nbsp;CONTACT</span>
  <span class="addr">LSWFSG c/o Nora Pell - Treasure , P.O. Box 418, Cedar Hollow, TX 70000</span>
  <span class="copy">©2014 wetland flora stewardship guild. All rights reserved.</span>
</footer>
</body>
</html>
```